Graphic design on webpages considering optimisation

Hi,

I would like to make the pages of my website look better. The looks must tie with the landing page, which I will not change.

Ping me an email with any questions. I have been on Pixel Harbour for the brimtower.com page and am very pleased with its looks.

Industry/Entity Type

Graphic Design

```html
<!DOCTYPE html>
<html lang="fr">
<head>
<meta charset="utf-8">
<title>BRIMTOWER – Avantages LedgerSuite</title>
<link href="https://fonts.googleapis.com/css2?family=Arimo:ital,wght@0,400;0,700;1,400&family=PT+Serif:wght@700&display=swap" rel="stylesheet">
<style>
:root{
  --blue:#1f78b4;
  --blue-dark:#1a6aa0;
  --side:#2a7fbd;
  --red:#f93e55;
  --orange:#fdb12a;
  --sky:#3a9fd8;
  --teal:#5aafad;
  --text:#444;
  --muted:#666;
  --gold:#f7c331;
  --gold-text:#a26a0d;
  --green:#5aaa3a;
  --line:#d8d8d8;
  --footer:#0d0d0d;
  --brick:#d24b2b;
}
*{margin:0;padding:0;box-sizing:border-box}
html,body{width:951px;height:1200px;overflow:hidden;background:#fff;font-family:"Arimo",Arial,sans-serif;color:var(--text)}
.page{position:relative;width:951px;height:1200px}
.header{position:absolute;left:135px;top:0;width:680px;height:76px;background:linear-gradient(#fff,#f1f1f1)}
.brand{position:absolute;left:4px;top:30px;font-size:20px;font-weight:700;color:#777;letter-spacing:1px;display:flex;align-items:center;gap:6px}
.brand i{display:inline-block;width:10px;height:10px;background:var(--blue)}
.lang{position:absolute;left:345px;top:37px;font-size:8px;color:#444;display:flex;align-items:center;gap:5px}
.lang span.box{border:1px solid #bbb;border-radius:2px;background:#fff;padding:3px 6px;font-size:7.5px;display:flex;align-items:center;gap:4px}
.flag{width:12px;height:8px;background:#37508c;display:inline-block}
.phone{position:absolute;left:503px;top:34px;display:flex;align-items:center;gap:6px;font-family:"PT Serif",serif;font-size:12.5px;color:#2d5a8a}
.nav{position:absolute;left:135px;top:76px;width:680px;height:32px;background:linear-gradient(#fff,#e6e6e6);border-top:2px solid #e2e2e2;border-bottom:1px solid #ccc;display:flex}
.nav a{flex:1;text-align:center;font-size:9px;color:#222;text-decoration:none;line-height:30px;border-right:1px solid #ddd}
.nav a:first-child{text-align:left;padding-left:14px;flex:.8}
.nav a:last-child{border-right:none}
.side{position:absolute;left:135px;top:122px;width:127px}
.side a{display:block;height:24.5px;margin-bottom:1.3px;background:var(--side);color:#fff;font-size:8px;line-height:24.5px;padding-left:13px;text-decoration:none;position:relative}
.side a::after{content:"";position:absolute;right:9px;top:9px;border:3px solid transparent;border-left:4px solid #9cc6e6}
.main{position:absolute;left:282px;top:128px;width:383px}
h2{font-size:11.5px;font-weight:400;color:var(--blue);letter-spacing:.2px}
.tiles{display:flex;gap:10px;margin-top:14px}
.tile{width:120px;height:120px;color:#fff;display:flex;flex-direction:column;align-items:center;justify-content:center;font-size:12px;gap:8px}
.tile svg{width:60px;height:44px}
.t-red{background:var(--red)}.t-org{background:var(--orange);margin-left:0}.t-sky{background:var(--sky);margin-left:4px}.t-teal{background:var(--teal)}
.docs{margin-top:21px}
.values{margin-top:24px}
.values p{font-size:7.8px;line-height:17px;text-align:justify;margin-top:8px;padding-left:2px}
.values p+p{margin-top:17px}
.module{font-size:7.8px;font-weight:700;color:var(--blue);margin-top:17px;padding-left:2px}
.intro{font-size:7.8px;line-height:17px;color:#222;margin-top:6px;padding-left:2px}
.feat{margin-top:8px}
.feat h3{font-size:7.8px;font-weight:400;color:var(--blue-dark);padding-left:16px;position:relative;line-height:14px}
.feat h3::before{content:"";position:absolute;left:3px;top:4px;width:6px;height:6px;border-radius:50%;background:var(--green)}
.feat p{font-size:7.5px;line-height:17px;color:var(--muted);padding-left:16px;text-align:justify;margin-top:3px;margin-bottom:9px}
.aside{position:absolute;left:688px;top:128px;width:127px}
.aside h4{font-size:9.5px;color:var(--blue);font-weight:700;margin-bottom:9px}
.btn{display:block;height:24px;background:var(--gold);border:1px solid #e0a616;color:var(--gold-text);font-size:8px;line-height:22px;padding-left:13px;margin-bottom:6px}
.partner{border:2px solid #e4e4e4;padding:7px;margin-bottom:20px}
.badge{display:flex;align-items:center;gap:6px;height:43px;padding-left:5px;font-size:11px;font-weight:700;color:#222}
.badge i{width:18px;height:18px;background:#1e4f7a;display:block}
.badge2{height:48px;background:#f6f6f6;border:1px solid #ddd;display:flex;align-items:center;padding-left:8px;font-size:12px;color:#444}
.quote{font-size:7px;font-style:italic;line-height:13.6px;color:#555;margin:10px 0 0 3px}
.arrows{display:flex;gap:2px;margin:10px 0 14px 3px}
.arrows span{width:13px;height:13px;background:var(--brick);display:flex;align-items:center;justify-content:center}
.footer{position:absolute;left:135px;top:1148px;width:680px;height:52px;background:var(--footer);color:#fff}
.flinks{position:absolute;left:13px;top:8px;font-size:8px;display:flex;gap:8px}
.flinks b{font-weight:400;color:#fff}
.copy{position:absolute;left:14px;top:33px;font-size:6.5px;color:#aaa}
.social{position:absolute;right:10px;top:11px;display:flex;align-items:center;gap:4px;font-size:7.5px;color:#ddd}
.social span{margin-right:10px}
.social i{width:22px;height:22px;border-radius:50%;background:#3b78a8;border:2px solid #cfdbe6;display:block}
</style>
</head>
<body>
<div class="page">
  <header class="header">
    <div class="brand"><i></i>BRIMTOWER</div>
    <div class="lang">Select Language :
      <span class="box"><span class="flag"></span>English
        <svg width="6" height="4" viewBox="0 0 6 4"><path d="M0 0l3 4 3-4z" fill="#333"/></svg></span>
    </div>
    <div class="phone">
      <svg width="15" height="14" viewBox="0 0 15 14"><rect width="15" height="14" rx="2" fill="#2f6fb3"/><path d="M4 3c1 0 2 2 1.5 3L7 8c1-.5 3 .5 3 1.5L9 11C6 11 3 7 3 4z" fill="#fff"/></svg>
      +33(0)145 550 123
    </div>
  </header>

  <nav class="nav">
    <a>Accueil</a><a>Produits</a><a>Valeurs Ajoutées</a><a>Clients</a><a>Service</a><a>Société</a><a>Contact</a>
  </nav>

  <aside class="side">
    <a>Nos Services</a><a>Conseil</a><a>Support</a><a>Developpement</a><a>Formation</a><a>Decouverte</a>
  </aside>

  <main class="main">
    <h2>AVANTAGES LEDGERSUITE</h2>
    <div class="tiles">
      <div class="tile t-red">
        <svg viewBox="0 0 60 44" fill="none" stroke="#fff" stroke-width="3"><path d="M14 40a10 10 0 010-20 16 16 0 0130-4 12 12 0 012 24z"/><circle cx="31" cy="26" r="6" stroke-width="2"/><circle cx="31" cy="26" r="2" stroke-width="1.5"/></svg>
        Manufacturing
      </div>
      <div class="tile t-org">
        <svg viewBox="0 0 60 44" fill="none" stroke="#fff" stroke-width="3"><path d="M14 40a10 10 0 010-20 16 16 0 0130-4 12 12 0 012 24z"/><path d="M22 20h12v10H22zM34 24h5l3 3v3h-8" stroke-width="1.8"/><circle cx="26" cy="32" r="2" stroke-width="1.5"/><circle cx="38" cy="32" r="2" stroke-width="1.5"/></svg>
        Distribution
      </div>
      <div class="tile t-sky">
        <svg viewBox="0 0 60 44" fill="none" stroke="#fff" stroke-width="3"><path d="M14 40a10 10 0 010-20 16 16 0 0130-4 12 12 0 012 24z"/><path d="M24 24h4v10h-4zM28 24l4-7c2 0 2 2 1 5h6c1 0 2 1 1 3l-2 8h-10" stroke-width="1.8"/></svg>
        Services
      </div>
    </div>

    <h2 class="docs">DOCUMENTATION</h2>
    <div class="tiles">
      <div class="tile t-teal">
        <svg viewBox="0 0 60 44" fill="none" stroke="#fff" stroke-width="3"><path d="M14 40a10 10 0 010-20 16 16 0 0130-4 12 12 0 012 24z"/><circle cx="33" cy="24" r="6" stroke-width="2"/><path d="M29 28l-6 6" stroke-width="2.5"/></svg>
        Héberger ou pas?
      </div>
    </div>

    <section class="values">
      <h2>VALEURS AJOUTÉES</h2>
      <p>La très grande majorité d'entre vous est aujourd'hui déjà équipée en progiciel de gestion, alors on peut se demander légitimement : pourquoi changer ?</p>
      <p>Parce que la suite logicielle LedgerSuite apporte de réels bénéfices, que l'on va détailler ci-dessous… et illustrer de manière personnalisée à votre cas, si vous nous laissez quelques petites informations dans le formulaire suivant : remplir le formulaire</p>
      <div class="module">LE MODULE LEDGERSUITE ENTREPRISE COMPREND :</div>
      <div class="intro">LedgerSuite CRM + : ce logiciel peut aussi s'installer de manière indépendante de LedgerSuite ERP ou de LedgerSuite Ecommerce. Elle inclut :</div>

      <div class="feat">
        <h3>GESTION DU MARKETING :</h3>
        <p>Tableau de bord, saisie des plans d'action marketing, projets et tâches relevant de ces plans, suivi opérationnel et budgétaire, mesure des retours sur investissement, campagnes de marketing, notamment d'emailing, activités, analyse des réceptions, ouvertures d'email et de cliques affichant le contact qui aura cliqué et le lien qui aura été cliqué.</p>
        <h3>GESTION DES VENTES ET DES FORCES COMMERCIALES:</h3>
        <p>Tableau de bord, pistes commerciales, prospects, clients, contacts, opportunités, devis, visualisation des articles, des prix et des disponibilités, suivi des commandes, visualisation des cas du support technique, prévisions commerciales, outils collaboratifs, possibilité de création et de partage de base de données « sales kit », gestion des notes de frais, visualisation des commissions, activités, saisie des feuille de temps.</p>
        <h3>GESTION DU SERVICE CLIENT :</h3>
        <p>Tableau de bord, cas client, visualisation des informations nécessaires au gestionnaire (dossier client, données financières), affectation, suivi, priorisation et escalade des cas client, emails LedgerSuite inclus ou rattachement d'emails Mailbox ou webmail, ouverture de cas et consultation self-service en ligne, possibilité de créer une base de données de connaissances ouverte aux employés comme aux clients 24h/24, 7j/7, et organisée par thème et niveau, gestion du temps affecté aux cas.</p>
        <h3>GESTION DES PARTENAIRES:</h3>
        <p>Tableau de bord, partenaires, activités partagées déclarées (actions marketing, actions commerciales, pistes commerciales, prospects, opportunités, prévisions commerciales, activités, commandes, commissions,…), plus les fonctionnalités de base de gestion du marketing, des ventes et des forces commerciales.</p>
      </div>
    </section>
  </main>

  <aside class="aside">
    <h4>UNE INFO ?</h4>
    <a class="btn">CONTACTEZ NOUS</a>
    <a class="btn">DEMANDE DE DEVIS</a>
    <h4 style="margin-top:13px">NOS PARTENARIATS</h4>
    <div class="partner"><div class="badge"><i></i>LEDGERSUITE</div></div>
    <h4>NOS PARTENARIATS</h4>
    <div class="partner">
      <div class="badge2">Bloomcart.com</div>
      <p class="quote">Producer of Synthetic Motor Oils Founded in 1839 Saves $100,000 Annually on Programming Costs Alone</p>
      <div class="arrows">
        <span><svg width="5" height="7" viewBox="0 0 5 7"><path d="M4 0L1 3.5 4 7" stroke="#fff" fill="none"/></svg></span>
        <span><svg width="5" height="7" viewBox="0 0 5 7"><path d="M1 0l3 3.5L1 7" stroke="#fff" fill="none"/></svg></span>
      </div>
    </div>
  </aside>

  <footer class="footer">
    <div class="flinks"><b>Accueil</b>I<b>Modules</b>I<b>Services</b>I<b>Prix</b>I<b>Société</b>I<b>Contact</b></div>
    <div class="copy">Copyright © 2013 BRIMTOWER | All right reserved</div>
    <div class="social"><span>Resaux sociaux</span><i></i><i></i><i></i></div>
  </footer>
</div>
</body>
</html>
```